4th Generation Family Business Needs a New Card Design!

We are a family owned 4th Generation company. We are based in the Sydney, Australia area and we are desperately in need of a more modern and classy card. We are monumental masons who design, supply & erect lasting memorials throughout cemeteries in Sydney. Our customers are normally in a period of grieving. I have attached logo files that will need to be implemented on the card. Company was established 1935. Australian Owned and Operated. Card needs to be designed to PIXO.com specification.

Target Market(s)

Our target market is based upon people that a grieving for family members that have passed away. We also deal with alot of companies that own and operate cemeteries.

Industry/Entity Type

Business

Contact Information for Business Card

Simon Harcourt, Operations Manager, 0417293086, simon@harcourtmemorials.com.au
Lewis Harcourt, Director, 0491630572, lewis@harcourtmemorials.com.au
Phone # 02 9561 3048
Website: www.harcourtmemorials.com.au
Address: Suite 17, 8 Palfrey Lane, West Carlow, Sydney NSW 2156

Font styles to use
Serif
Decorative
Script

Requirements
Must have
• Would like to see the logo nicely implemented with a modern design. Embossed lettering would be a nice additive.

```html
<!DOCTYPE html>
<html lang="en">
<head>
<meta charset="utf-8">
<title>Harcourt Memorials – Business Card</title>
<link rel="stylesheet" href="https://fonts.googleapis.com/css2?family=Cinzel:wght@400;600&family=Noto+Serif:ital@0;1&display=swap">
<style>
  :root {
    --backdrop: #e6e6e6;
    --ink: #121212;
    --card-black: #0c0c0c;
    --card-white: #fbfbfb;
    --gold: #d4ae2c;
    --gold-deep: #b8941c;
    --text-light: #f2f2f2;
    --text-dark: #1a1a1a;
  }
  * { box-sizing: border-box; margin: 0; padding: 0; }
  html, body {
    width: 1200px; height: 576px; overflow: hidden;
    background: var(--backdrop);
  }
  .canvas { position: relative; width: 1200px; height: 576px; }

  .card {
    position: absolute;
    top: 138px;
    overflow: hidden;
  }

  /* Front */
  .card--front {
    left: 81px; width: 485px; height: 294px;
    background: radial-gradient(ellipse at 38% 35%, #2a2a2a 0%, var(--card-black) 55%);
  }
  .card--front .brand {
    position: absolute; left: 0; right: 0; top: 122px;
    text-align: center;
    font-family: "Cinzel", serif; font-weight: 400;
    color: var(--text-light);
    line-height: 1;
  }
  .brand__name { display: block; font-size: 38px; letter-spacing: 1px; }
  .brand__sub { display: block; font-size: 17px; letter-spacing: 2px; margin-top: 6px; }
  .card--front .edge-band {
    position: absolute; left: 0; right: 0; bottom: 0; height: 10px;
    background: linear-gradient(180deg, var(--gold), var(--gold-deep));
  }

  /* Back */
  .card--back {
    left: 602px; width: 482px; height: 292px;
    background: var(--card-white);
  }
  .card--back .wave { position: absolute; inset: 0; }
  .card--back .brand {
    position: absolute; left: 22px; width: 220px; top: 146px;
    text-align: center;
    font-family: "Cinzel", serif; font-weight: 400;
    color: var(--text-dark);
    line-height: 1;
  }
  .card--back .brand__name { font-size: 31px; }
  .card--back .brand__sub { font-size: 14px; }

  .person {
    position: absolute; right: 23px; top: 22px; text-align: right;
    color: var(--text-dark);
  }
  .person__name {
    font-family: "Cinzel", serif; font-weight: 600;
    font-size: 21px; letter-spacing: 0.5px; line-height: 1;
  }
  .person__role {
    font-family: "Noto Serif", serif; font-style: italic;
    font-size: 11.5px; margin-top: 4px;
  }
  .address {
    position: absolute; right: 23px; top: 84px; text-align: right;
    font-family: "Noto Serif", serif; font-size: 12px; line-height: 18px;
    color: var(--text-dark);
  }
  .contacts {
    position: absolute; right: 22px; top: 208px;
    list-style: none; text-align: right;
    font-family: "Noto Serif", serif; font-size: 12px; line-height: 16.6px;
    color: var(--text-light);
  }
  .contacts li { display: flex; justify-content: flex-end; align-items: center; gap: 6px; }
  .contacts svg { width: 9px; height: 9px; fill: var(--gold); flex: none; }
</style>
</head>
<body>
<main class="canvas">

  <section class="card card--front" aria-label="Card front">
    <div class="brand">
      <span class="brand__name">HARCOURT</span>
      <span class="brand__sub">MEMORIALS</span>
    </div>
    <div class="edge-band"></div>
  </section>

  <section class="card card--back" aria-label="Card back">
    <svg class="wave" viewBox="0 0 482 292" preserveAspectRatio="none" aria-hidden="true">
      <path fill="var(--gold)" d="M0,224 C130,286 300,218 482,134 L482,292 L0,292 Z"/>
      <path fill="var(--card-white)" d="M0,234 C130,296 300,228 482,144 L482,292 L0,292 Z"/>
      <path fill="var(--gold)" d="M40,250 C160,300 320,236 482,158 L482,292 L40,292 Z"/>
      <path fill="var(--card-black)" d="M0,246 C140,310 310,244 482,164 L482,292 L0,292 Z"/>
    </svg>

    <div class="brand">
      <span class="brand__name">HARCOURT</span>
      <span class="brand__sub">MEMORIALS</span>
    </div>

    <div class="person">
      <p class="person__name">SIMON HARCOURT</p>
      <p class="person__role">Operations Manager</p>
    </div>

    <p class="address">Suite 17, 8 Palfrey Lane,<br>West Carlow, Sydney NSW 2156</p>

    <ul class="contacts">
      <li>0491630572
        <svg viewBox="0 0 10 10"><path d="M2 0.5 L3.6 2.6 L2.8 3.6 C3.4 5 4.8 6.4 6.4 7.2 L7.4 6.4 L9.5 8 L8.4 9.5 C4.5 9.3 0.7 5.5 0.5 1.6 Z"/></svg>
      </li>
      <li>02 9561 3048
        <svg viewBox="0 0 10 10"><path d="M0.5 3 C3 1 7 1 9.5 3 L8.5 4.3 L7 3.8 L7 3 C5.6 2.6 4.4 2.6 3 3 L3 3.8 L1.5 4.3 Z M2 5 L8 5 L9 9 L1 9 Z"/></svg>
      </li>
      <li>harcourtmemorials.com.au
        <svg viewBox="0 0 10 10"><path d="M0.5 2 L9.5 2 L9.5 8 L0.5 8 Z M1.2 2.6 L5 5.4 L8.8 2.6 Z" fill-rule="evenodd"/></svg>
      </li>
      <li>lewis@harcourtmemorials.com.au
        <svg viewBox="0 0 10 10"><circle cx="5" cy="5" r="4.5"/></svg>
      </li>
    </ul>
  </section>

</main>
</body>
</html>
```